Finiding oppertunites in Real Estate 6.15.20

size of ad 7” x 9.6”
1-I like the ad to stand out and attract people's attention.
2-you should be able to see the text of the ad clearly .. see the attachment anything in yellow is instructions.
3-the list of topics should not be the main part of the ad
4-if you decide you want a picture or vector of a person .. (you decide)
then it should be a white male about 25-30 years old wearing a solid white or blue shirt and not long hair.
5-leave 1 inch for footer
see attachment
Good luck

Target Market(s)

potential male students 25-35 years of age

Industry/Entity Type

Education

Requirements
Must have
• will stand out and people would want to see it.
should be able to read the words of ad
Nice to have
• how to make money in real estate on one line

```html
<!DOCTYPE html>
<html lang="en">
<head>
<meta charset="UTF-8">
<title>Real Estate Career Course</title>
<link rel="stylesheet" href="https://fonts.googleapis.com/css2?family=Open+Sans:wght@400;600;700;800&display=swap">
<style>
  :root {
    --ink: #4f5154;
    --ink-dark: #3d3f42;
    --accent-blue: #0ea5ea;
    --accent-red: #ec4b57;
    --paper: #ffffff;
    --soft-grey: #e4e5e7;
    --rule: #555759;
  }
  * { margin: 0; padding: 0; box-sizing: border-box; }
  html, body {
    width: 743px;
    height: 1200px;
    overflow: hidden;
    background: var(--paper);
  }
  body {
    position: relative;
    font-family: "Open Sans", Arial, sans-serif;
    color: var(--ink);
  }
  .decor-texture {
    position: absolute;
    top: 0;
    right: 0;
    width: 430px;
    height: 760px;
    background:
      radial-gradient(ellipse at 85% 15%, rgba(190,192,196,0.55) 0%, rgba(220,221,224,0.35) 35%, rgba(255,255,255,0) 70%);
  }
  .line {
    position: absolute;
    left: 0;
    right: 0;
    text-align: center;
    white-space: nowrap;
  }
  .accent { color: var(--accent-blue); }
  .course-title {
    top: 92px;
    font-size: 39px;
    font-weight: 700;
    color: var(--ink);
  }
  .money-line {
    font-size: 31px;
    font-weight: 400;
    color: var(--ink);
  }
  .money-line strong { font-weight: 800; }
  .money-line .accent { font-weight: 800; }
  .money-line--one { top: 154px; }
  .money-line--two { top: 198px; }
  .money-line--two strong { color: var(--ink-dark); }
  .audience, .promise {
    font-size: 32px;
    font-weight: 800;
    color: var(--ink-dark);
  }
  .audience--one { top: 256px; }
  .audience--two { top: 299px; }
  .promise--one { top: 366px; }
  .promise--two { top: 413px; }
  .remote-badge {
    position: absolute;
    top: 490px;
    left: 270px;
    width: 196px;
    height: 44px;
    border-radius: 10px;
    background: linear-gradient(#f06570, var(--accent-red));
    color: #fff;
    font-size: 20px;
    font-weight: 700;
    line-height: 44px;
    text-align: center;
    box-shadow: 0 2px 3px rgba(0,0,0,0.15);
  }
  .session-count {
    top: 552px;
    font-size: 34px;
    font-weight: 800;
    color: var(--ink);
  }
  .start-date {
    position: absolute;
    top: 618px;
    left: 165px;
    width: 406px;
    height: 67px;
    border: 1.5px solid #6a6c6f;
    border-radius: 9px;
    overflow: hidden;
    display: flex;
  }
  .start-date__label {
    flex: 1;
    font-size: 33px;
    font-weight: 700;
    color: var(--ink);
    line-height: 64px;
    text-align: center;
  }
  .start-date__day {
    width: 141px;
    background: var(--accent-blue);
    color: #fff;
    font-size: 33px;
    font-weight: 800;
    line-height: 64px;
    text-align: center;
  }
  .house-visual {
    position: absolute;
    top: 722px;
    left: 204px;
    width: 338px;
    height: 224px;
    border-radius: 6px;
    background: linear-gradient(160deg, #8c9bb0 0%, #9b3a2c 45%, #7a2a20 65%, #c9a85a 100%);
  }
  .topics-heading {
    top: 968px;
    font-size: 24px;
    font-weight: 600;
    color: var(--accent-blue);
  }
  .topics-rule {
    position: absolute;
    top: 1010px;
    left: 347px;
    width: 50px;
    height: 3px;
    background: var(--rule);
  }
  .topics-list {
    position: absolute;
    top: 1027px;
    left: 110px;
    width: 523px;
    text-align: center;
    font-size: 12.6px;
    line-height: 19px;
    color: var(--ink-dark);
  }
</style>
</head>
<body>
  <div class="decor-texture" role="img" aria-label="Soft grey dotted diamond texture fading into the page"></div>

  <h1 class="line course-title">Real Estate Career Course</h1>
  <p class="line money-line money-line--one">How to <span class="accent">Make Money</span></p>
  <p class="line money-line money-line--two">in <strong>Real Estate?</strong></p>

  <p class="line audience audience--one">For those who have started or</p>
  <p class="line audience audience--two">would like to go into <span class="accent">Real Estate</span></p>

  <p class="line promise promise--one">An investment in knowledge</p>
  <p class="line promise promise--two">opens up untold <span class="accent">opportunities</span></p>

  <div class="remote-badge">Remote sessions</div>

  <p class="line session-count">12 session course</p>

  <div class="start-date">
    <span class="start-date__label">Classes starting</span>
    <span class="start-date__day">June 16</span>
  </div>

  <div class="house-visual" role="img" aria-label="Photo of a red brick model house with stacks of gold coins"></div>

  <h2 class="line topics-heading">A partial listing of Topics</h2>
  <div class="topics-rule"></div>
  <p class="topics-list">
    Single-family | Multifamily | Management | Real Estate Concepts | Real Estate law | Investment
    properties | Foreclosures Rehab | Foreclosures | Short sales | Development | Financial modeling<br>
    HUD properties | Due Diligence
  </p>
</body>
</html>
```